I need a website, primarily a landing page, for my company, Morrow Vantage. A sales training and cons

I need a web design/landing page for a new sales training and consulting company, morrow vantage. We perform "sales experiments" aimed at each individual or team, where we assist in helping them identify their strengths, through a series of "sales experiments" that we can tailor based on the individual and what they're trying to accomplish.

```html
<!DOCTYPE html>
<html lang="en">
<head>
<meta charset="utf-8">
<title>Morrow Vantage — Sales Training & Consulting</title>
<link href="https://fonts.googleapis.com/css2?family=Poppins:wght@400;500;600&family=Roboto:wght@400;500;700&family=Roboto+Condensed:wght@500&display=swap" rel="stylesheet">
<style>
:root{
  --blue:#1f7fd6;
  --blue-dark:#1566b3;
  --blue-deep:#0d4f96;
  --ink:#1b1b1b;
  --body:#444;
  --light:#f3f3f3;
  --footer:#0f0f0f;
  --white:#fff;
}
*{margin:0;padding:0;box-sizing:border-box}
html,body{width:1200px;height:3644px;overflow:hidden}
body{position:relative;background:var(--white);font-family:'Roboto',sans-serif;color:var(--body)}
.abs{position:absolute}
/* header */
.topbar{left:570px;top:0;width:630px;height:44px;background:var(--blue);clip-path:polygon(30px 0,100% 0,100% 100%,0 100%)}
.topbar-info{left:620px;top:12px;color:var(--white);font-size:14px;display:flex;gap:30px;align-items:center}
.topbar-info span{display:flex;gap:6px;align-items:center}
.social-squares{display:flex;gap:10px;margin-left:-10px}
.social-squares i{display:block;width:18px;height:18px;background:var(--white);border-radius:3px;opacity:.9}
.brand{left:90px;top:62px;display:flex;align-items:center;gap:10px;font-family:'Poppins',sans-serif;font-weight:600;font-size:20px;color:var(--blue-deep)}
.brand i{display:block;width:26px;height:26px;border-radius:50%;background:var(--blue-deep)}
.nav{left:420px;top:92px;display:flex;gap:42px;font-family:'Poppins',sans-serif;font-size:17px;color:var(--ink)}
.nav .active{color:var(--blue)}
/* hero */
.hero{left:0;top:155px;width:1200px;height:590px;background:linear-gradient(180deg,#2a2a33 0%,#8a4a22 35%,#d8802e 55%,#6a4a3a 80%,#3a3a40 100%)}
.hero-title{left:75px;top:318px;font-family:'Roboto Condensed',sans-serif;font-weight:500;font-size:76px;line-height:90px;color:var(--white);letter-spacing:1px}
.hero-sub{left:75px;top:424px;font-family:'Roboto Condensed',sans-serif;font-size:29px;color:var(--white)}
.dots{left:1160px;top:402px;display:flex;flex-direction:column;gap:10px}
.dots i{display:block;width:9px;height:9px;border-radius:50%;background:var(--white)}
.dots i:first-child{background:var(--blue)}
/* about */
.about-frame{left:85px;top:855px;width:440px;height:340px;background:var(--blue)}
.about-photo{left:108px;top:878px;width:440px;height:325px;background:linear-gradient(135deg,#c9ced4,#6b7580 60%,#2d3440);box-shadow:0 6px 18px rgba(0,0,0,.25)}
.about-kicker{left:600px;top:896px;font-family:'Poppins',sans-serif;font-size:27px;line-height:36px;color:var(--blue)}
.about-title{left:598px;top:928px;font-family:'Poppins',sans-serif;font-weight:400;font-size:46px;line-height:60px;color:var(--ink)}
.about-text{left:600px;top:992px;width:430px;font-size:14px;line-height:26px}
.btn{display:flex;align-items:center;justify-content:center;background:var(--blue);color:var(--white);font-size:16px;border-radius:3px}
.about-btn{left:600px;top:1154px;width:145px;height:36px}
/* services */
.services{left:0;top:1310px;width:1200px;height:660px;background:linear-gradient(135deg,#1d6fc2 0%,#2f8ae0 50%,#1a63b3 100%)}
.services-title{left:0;top:1392px;width:1200px;text-align:center;font-family:'Poppins',sans-serif;font-weight:400;font-size:44px;line-height:60px;color:var(--white)}
.card{width:315px;height:330px;top:1520px;background:var(--white);text-align:center;padding-top:38px}
.card-base{width:315px;height:32px;top:1850px;background:var(--blue-dark)}
.card.featured{background:var(--blue-dark);border:2px solid rgba(255,255,255,.5)}
.card h3{font-family:'Poppins',sans-serif;font-weight:500;font-size:23px;color:var(--ink);margin-top:16px}
.card p{font-size:14px;line-height:25px;width:250px;margin:10px auto 0}
.card.featured h3,.card.featured p{color:var(--white)}
/* team */
.team-box{left:88px;top:2127px;width:610px;height:373px;border:2px solid var(--blue)}
.team-title{left:122px;top:2172px;font-family:'Poppins',sans-serif;font-weight:400;font-size:32px;line-height:44px;color:var(--ink)}
.team-text{left:122px;top:2228px;width:465px;font-size:14px;line-height:27px}
.team-btn{left:120px;top:2420px;width:112px;height:34px;font-size:15px}
.team-video{left:595px;top:2142px;width:513px;height:341px;background:linear-gradient(160deg,#3a3d42,#8d9096 55%,#2b2d31)}
/* blog */
.blog{left:0;top:2615px;width:1200px;height:615px;background:var(--light)}
.blog-title{left:0;top:2670px;width:1200px;text-align:center;font-family:'Poppins',sans-serif;font-weight:400;font-size:44px;line-height:60px;color:var(--ink)}
.post{top:2785px;width:315px}
.post-img{height:205px;border:4px solid var(--white);box-shadow:0 3px 10px rgba(0,0,0,.25)}
.post-date{margin-top:30px;font-size:14px;color:var(--blue)}
.post h3{margin-top:10px;font-family:'Poppins',sans-serif;font-weight:500;font-size:20px;color:var(--ink)}
.post p{margin-top:8px;font-size:14px;line-height:23px}
/* footer */
.footer{left:0;top:3230px;width:1200px;height:414px;background:var(--footer)}
.f-head{top:3308px;font-family:'Poppins',sans-serif;font-weight:400;font-size:17px;color:var(--white)}
.f-list{color:var(--white);font-size:14px}
.f-contact{left:98px;top:3362px;display:flex;flex-direction:column;gap:22px;width:240px;line-height:21px}
.f-contact div{display:flex;gap:16px;align-items:flex-start}
.f-links{left:400px;top:3362px;display:flex;flex-direction:column;gap:6px;font-size:13px}
.f-links span::before{content:"▸";margin-right:10px;font-size:10px}
.f-follow{left:612px;top:3368px;display:flex;flex-direction:column;gap:22px;font-size:15px}
.f-follow span{display:flex;gap:12px;align-items:center}
.f-follow i{display:block;width:24px;height:24px;border:1.5px solid var(--white);border-radius:50%}
.field{left:828px;width:274px;height:36px;background:var(--white);color:#555;font-size:15px;padding:9px 12px}
.send{left:828px;top:3465px;width:122px;height:36px;font-size:17px;letter-spacing:1px;border-radius:0}
.f-rule{left:0;top:3560px;width:1200px;height:1px;background:#2a2a2a}
.copy{left:0;top:3594px;width:1200px;text-align:center;font-size:14px;color:var(--white)}
</style>
</head>
<body>
<header>
  <div class="abs topbar"></div>
  <div class="abs topbar-info">
    <span><svg width="14" height="14" viewBox="0 0 24 24"><path fill="#fff" d="M6.6 10.8a15 15 0 0 0 6.6 6.6l2.2-2.2c.3-.3.7-.4 1-.2 1.1.4 2.3.6 3.6.6.6 0 1 .4 1 1V20c0 .6-.4 1-1 1A17 17 0 0 1 3 4c0-.6.4-1 1-1h3.5c.6 0 1 .4 1 1 0 1.3.2 2.5.6 3.6.1.3 0 .7-.2 1z"/></svg>0300 555 0182</span>
    <span><svg width="14" height="12" viewBox="0 0 24 20"><rect x="1" y="1" width="22" height="18" fill="none" stroke="#fff" stroke-width="2"/><path d="M1 1l11 9 11-9" fill="none" stroke="#fff" stroke-width="2"/></svg>hello@morrowvantage.example</span>
    <div class="social-squares"><i></i><i></i><i></i><i></i></div>
  </div>
  <div class="abs brand"><i></i>Morrow Vantage</div>
  <nav class="abs nav">
    <span class="active">Home</span><span>About us</span><span>Services</span><span>Benefits</span><span>News &amp; Blogs</span><span>Contact Us</span>
  </nav>
</header>

<section>
  <div class="abs hero" role="img" aria-label="Snow-capped mountain peak under an orange sunset sky"></div>
  <h1 class="abs hero-title">MORROW VANTAGE</h1>
  <p class="abs hero-sub">Optimize Performance in Business &amp; in Life</p>
  <div class="abs dots"><i></i><i></i><i></i><i></i></div>
</section>

<section>
  <div class="abs about-frame"></div>
  <div class="abs about-photo" role="img" aria-label="Two businessmen in suits talking across a meeting table with a laptop"></div>
  <p class="abs about-kicker">About</p>
  <h2 class="abs about-title">Morrow Vantage</h2>
  <p class="abs about-text">The point of using Lorem Ipsum is that it has a more-or-less normal distribution of letters, as opposed to using 'Content here, content here', making it look like readable English. Many desktop publishing packages and web page editors now use Lorem Ipsum as their default model text, and a search for 'lorem ipsum' will uncover many web sites still in their infancy.</p>
  <div class="abs btn about-btn">Read More</div>
</section>

<section>
  <div class="abs services"></div>
  <h2 class="abs services-title">Our Services</h2>

  <div class="abs card-base" style="left:95px"></div>
  <div class="abs card" style="left:95px">
    <svg width="90" height="90" viewBox="0 0 90 90" fill="none" stroke="#1566b3" stroke-width="2.5"><rect x="14" y="10" width="62" height="50" rx="3"/><circle cx="32" cy="70" r="7"/><path d="M20 88c0-8 6-11 12-11s12 3 12 11"/><circle cx="62" cy="30" r="7"/><path d="M50 48c0-8 6-11 12-11s12 3 12 11"/><path d="M28 28h14l-5-5M42 28l-5 5"/><text x="36" y="52" font-size="16" fill="#1566b3" stroke="none" font-family="Roboto,sans-serif">?</text></svg>
    <h3>Sales Experiments</h3>
    <p>The point of using Lorem Ipsum is that it has a more-or-less normal distribution of letters, as opposed to using</p>
  </div>

  <div class="abs card-base" style="left:447px"></div>
  <div class="abs card featured" style="left:447px">
    <svg width="90" height="90" viewBox="0 0 90 90" fill="none" stroke="#fff" stroke-width="2.5"><rect x="22" y="12" width="46" height="30" rx="3"/><circle cx="45" cy="52" r="6"/><path d="M33 72c0-8 6-12 12-12s12 4 12 12"/><circle cx="18" cy="58" r="5"/><path d="M8 78c0-6 4-9 10-9s10 3 10 9"/><circle cx="72" cy="58" r="5"/><path d="M62 78c0-6 4-9 10-9s10 3 10 9"/><path d="M10 84h70"/><path d="M30 22h30M30 30h20"/></svg>
    <h3>Consulting</h3>
    <p>The point of using Lorem Ipsum is that it has a more-or-less normal distribution of letters, as opposed to using</p>
  </div>

  <div class="abs card-base" style="left:792px"></div>
  <div class="abs card" style="left:792px">
    <svg width="90" height="90" viewBox="0 0 90 90" fill="none" stroke="#1566b3" stroke-width="2.5"><rect x="8" y="12" width="66" height="48" rx="3"/><path d="M30 60v10h22V60M24 70h34"/><path d="M18 24h24M18 32h18M18 40h22"/><circle cx="56" cy="42" r="12"/><path d="M65 51l14 14"/></svg>
    <h3>Sales Training</h3>
    <p>The point of using Lorem Ipsum is that it has a more-or-less normal distribution of letters, as opposed to using</p>
  </div>
</section>

<section>
  <div class="abs team-box"></div>
  <h2 class="abs team-title">Team Work</h2>
  <p class="abs team-text">It is a long established fact that a reader will be distracted by the readable content of a page when looking at its layout. The point of using Lorem Ipsum is that it has a more-or-less normal distribution of letters, as opposed to using 'Content here, content here', making it look like readable English. Many desktop publishing packages and web page editors now use Lorem Ipsum as their default</p>
  <div class="abs btn team-btn">Learn More</div>
  <div class="abs team-video" role="img" aria-label="Business team gathered around a laptop in a modern office"></div>
  <svg class="abs" style="left:808px;top:2268px" width="80" height="80" viewBox="0 0 80 80"><circle cx="40" cy="40" r="36" fill="#fff" fill-opacity=".85"/><circle cx="40" cy="40" r="30" fill="#1b1b1b"/><path d="M33 26l20 14-20 14z" fill="#fff"/></svg>
</section>

<section>
  <div class="abs blog"></div>
  <h2 class="abs blog-title">Latest Blog</h2>
  <article class="abs post" style="left:90px">
    <div class="post-img" role="img" aria-label="Hands on a laptop keyboard beside printed charts" style="background:linear-gradient(135deg,#2b3440,#6f7c8c 55%,#d5dce4)"></div>
    <p class="post-date">July 12,2018</p>
    <h3>Neque porro quisquam</h3>
    <p>It is a long established fact that a reader will be distracted by the readable content</p>
  </article>
  <article class="abs post" style="left:437px">
    <div class="post-img" role="img" aria-label="Colleagues working together at a desktop computer" style="background:linear-gradient(135deg,#e9ecef,#9aa3ac 55%,#3b4148)"></div>
    <p class="post-date">July 12,2018</p>
    <h3>Dolorem ipsum quia</h3>
    <p>It is a long established fact that a reader will be distracted by the readable content</p>
  </article>
  <article class="abs post" style="left:785px">
    <div class="post-img" role="img" aria-label="Person typing on a laptop with data on screen" style="background:linear-gradient(135deg,#5a6470,#2a2f36 50%,#8d97a2)"></div>
    <p class="post-date">July 12,2018</p>
    <h3>Porro quisquam est qui</h3>
    <p>It is a long established fact that a reader will be distracted by the readable content</p>
  </article>
</section>

<footer>
  <div class="abs footer"></div>
  <h4 class="abs f-head" style="left:98px">CONTACT US</h4>
  <h4 class="abs f-head" style="left:392px">QUICK LINKS</h4>
  <h4 class="abs f-head" style="left:612px">FOLLOW US</h4>
  <h4 class="abs f-head" style="left:828px">NEWSLETTER</h4>
  <div class="abs f-list f-contact">
    <div><svg width="14" height="18" viewBox="0 0 14 18"><path d="M7 0a7 7 0 0 0-7 7c0 5 7 11 7 11s7-6 7-11a7 7 0 0 0-7-7zm0 10a3 3 0 1 1 0-6 3 3 0 0 1 0 6z" fill="#fff"/></svg><span>12, Fenwick Row, Elmbridge,<br>WA 6102</span></div>
    <div><svg width="14" height="14" viewBox="0 0 24 24"><path fill="#fff" d="M6.6 10.8a15 15 0 0 0 6.6 6.6l2.2-2.2c.3-.3.7-.4 1-.2 1.1.4 2.3.6 3.6.6.6 0 1 .4 1 1V20c0 .6-.4 1-1 1A17 17 0 0 1 3 4c0-.6.4-1 1-1h3.5c.6 0 1 .4 1 1 0 1.3.2 2.5.6 3.6.1.3 0 .7-.2 1z"/></svg><span>08 5550 2741</span></div>
    <div><svg width="14" height="12" viewBox="0 0 24 20"><rect x="1" y="1" width="22" height="18" fill="#fff"/><path d="M1 1l11 9 11-9" fill="none" stroke="#0f0f0f" stroke-width="2"/></svg><span>team@morrowvantage.example</span></div>
  </div>
  <div class="abs f-list f-links"><span>Home</span><span>About us</span><span>Product</span><span>Services</span><span>Contact Us</span></div>
  <div class="abs f-list f-follow"><span><i></i>Circlenet</span><span><i></i>Chirpline</span><span><i></i>Orbitplus</span></div>
  <div class="abs field" style="top:3368px">Your Name</div>
  <div class="abs field" style="top:3415px">Email address</div>
  <div class="abs btn send">SEND</div>
  <div class="abs f-rule"></div>
  <p class="abs copy">© Copyright 2018 . All Rights Reserved.</p>
</footer>
</body>
</html>
```